we are an outdoor outlet in a country club that has a variety of outlets. The Club is called Meadowlark and is located in Cairo, Egypt. This garden menu will include cuisines from the Mediterranean, Asia and Texmex. we need a menu that is colorful and would fit an A3 size, back and front are to be used. Attached is the old menu currently in use (Garden Menu 2012.pdf is just for reference) and the new menu text for you to use is under the name Garden Menu Fall 2013
thank you.
Updates
Logo files have been uploaded for this project
Industry/Entity Type
Club
Look and feel
Each slider illustrates characteristics of the customer's brand and the style your logo design should communicate.

```html
<!DOCTYPE html>
<html lang="en">
<head>
<meta charset="utf-8">
<title>Garden Menu – Meadowlark Country Club</title>
<link href="https://fonts.googleapis.com/css2?family=Raleway:wght@400;500;800&family=Quicksand:wght@700&family=Arvo&display=swap" rel="stylesheet">
<style>
:root{
  --paper:#f5e3bd;
  --paper-light:#fbf0d6;
  --maroon:#8b2b2c;
  --item:#7d3a2e;
  --desc:#c4462a;
  --orange:#ef6b2d;
  --orange-dark:#d9531c;
  --ribbon:#d8d45c;
  --fold:#6e2a20;
  --ink:#3b2a24;
  --white:#ffffff;
}
*{margin:0;padding:0;box-sizing:border-box}
html,body{width:848px;height:1200px;overflow:hidden}
body{background:var(--paper)}
.menu{position:relative;width:848px;height:1200px;overflow:hidden;
  background:radial-gradient(ellipse at 50% 40%,var(--paper-light) 0%,var(--paper) 70%,#efd5a4 100%);
  font-family:'Raleway',sans-serif}
.frame{position:absolute;left:24px;top:30px;width:797px;height:1135px;border:3px solid var(--white)}
.frame-inner{position:absolute;left:34px;top:40px;width:777px;height:1115px;border:1px dashed var(--white)}
.title{position:absolute;left:101px;top:52px;font-weight:800;font-size:49px;color:var(--maroon);letter-spacing:1px}
.brand{position:absolute;left:580px;top:60px;display:flex;align-items:center;gap:10px;
  font-family:'Raleway',sans-serif;font-weight:500;font-size:25px;color:#5a5a55}
.brand-dot{width:28px;height:28px;border-radius:50%;background:#9cc23a}
.ribbon{position:absolute;height:30px;background:var(--ribbon)}
.tag{position:absolute;background:var(--orange);color:var(--white);font-weight:400;font-size:29px;
  display:flex;align-items:center;justify-content:center;letter-spacing:.5px}
.fold{position:absolute;width:0;height:0}
.sub{position:absolute;font-family:'Quicksand',sans-serif;font-size:20px;color:var(--maroon);text-align:center}
.rule{position:absolute;height:0;border-top:1px dotted #c9b46a}
.sprig{position:absolute;width:10px;height:10px;border-radius:50%;background:#c9c24a}
.list{position:absolute;list-style:none}
.item{position:relative}
.name{font-size:11.5px;text-transform:uppercase;color:var(--item);letter-spacing:.3px}
.desc{font-family:'Arvo',serif;font-size:9.5px;line-height:12.5px;color:var(--desc)}
.price{position:absolute;top:0;font-size:11.5px;color:var(--item)}
.panel{position:absolute;background:var(--orange);border-radius:18px;box-shadow:2px 4px 6px rgba(90,40,10,.35)}
.panel-dash{position:absolute;inset:10px;border:1px dashed rgba(255,255,255,.8);border-radius:12px}
.panel h3{position:absolute;left:0;right:0;text-align:center;font-family:'Quicksand',sans-serif;font-size:24px;line-height:22px;color:var(--ink)}
.panel .rule{border-top:1px solid rgba(255,240,220,.7)}
.panel .sprig{background:#fbe3cf}
.panel .name{color:var(--white);font-size:14px}
.panel .desc{color:var(--white);font-size:11px;line-height:15px}
.panel .price{color:var(--white);font-size:14px}
.art{position:absolute;border-radius:50%}
.badge{position:absolute;left:372px;top:1072px;width:100px;height:100px;border-radius:50%;background:var(--orange-dark);
  border:2px solid #f39a6a;color:var(--white);font-family:'Arvo',serif;font-size:8.5px;line-height:10px;
  display:flex;align-items:center;justify-content:center;text-align:center;text-transform:uppercase;padding:10px}
.badge b{font-weight:700}
</style>
</head>
<body>
<div class="menu">
  <div class="frame"></div>
  <div class="frame-inner"></div>

  <h1 class="title">GARDEN MENU</h1>
  <div class="brand"><span class="brand-dot"></span>meadowlark</div>

  <!-- Asian Corner heading -->
  <div class="ribbon" style="left:0;top:141px;width:350px"></div>
  <div class="tag" style="left:104px;top:127px;width:244px;height:41px">ASIAN CORNER</div>
  <div class="fold" style="left:104px;top:168px;border-top:12px solid var(--fold);border-left:22px solid transparent"></div>

  <!-- Tex Mex heading -->
  <div class="ribbon" style="left:600px;top:141px;width:248px"></div>
  <div class="tag" style="left:600px;top:127px;width:134px;height:41px">TEX MEX</div>
  <div class="fold" style="left:712px;top:168px;border-top:12px solid var(--fold);border-right:22px solid transparent"></div>
  <div class="art" role="img" aria-label="Drawing of a sombrero" style="left:482px;top:128px;width:118px;height:50px;background:radial-gradient(ellipse,#e7d8b4 0%,#c9b68c 70%,rgba(201,182,140,0) 100%)"></div>

  <!-- Asian salads -->
  <div class="sub" style="left:95px;top:183px;width:290px">salads &amp; appetizer</div>
  <div class="rule" style="left:95px;top:218px;width:290px"></div>
  <div class="sprig" style="left:235px;top:209px"></div>
  <ul class="list" style="left:100px;top:228px;width:285px">
    <li class="item" style="height:51px"><div class="name">Chicken Wasabi Salad</div><div class="desc">Diced chicken with a mayo wasabi<br>dressing on top of shredded lettuce</div><span class="price" style="left:270px">00</span></li>
    <li class="item" style="height:51px"><div class="name">Chicken Sesame Noodle Salad</div><div class="desc">Sesame crusted chicken with glass noodles<br>tossed with sweet chili, soy sauce, and lemongrass</div><span class="price" style="left:270px">00</span></li>
    <li class="item" style="height:50px"><div class="name">Spring Rolls</div><div class="desc">Vegetable spring rolls served with house made<br>sweet and sour dip</div><span class="price" style="left:270px">00</span></li>
    <li class="item"><div class="name">Indian Samosa</div><div class="desc">Fried dough parcels filled with<br>vegetables and spices</div><span class="price" style="left:270px">00</span></li>
  </ul>

  <!-- Tex Mex salads -->
  <div class="sub" style="left:455px;top:183px;width:290px">salads &amp; appetizer</div>
  <div class="rule" style="left:455px;top:218px;width:290px"></div>
  <div class="sprig" style="left:595px;top:209px"></div>
  <ul class="list" style="left:460px;top:228px;width:285px">
    <li class="item" style="height:51px"><div class="name">Caesar Salad</div><div class="desc">Iceberg lettuce with Caesar dressing with<br>grated Parmesan cheese and croutons</div><span class="price" style="left:270px">00</span></li>
    <li class="item" style="height:51px"><div class="name">Taco Salad</div><div class="desc">Chicken breast, beans, sour cream, guacamole,<br>tomato, corn, lettuce, olives, chives, vinaigrette</div><span class="price" style="left:270px">00</span></li>
    <li class="item" style="height:38px"><div class="name">Nachos</div><div class="desc">Topped with chili, melted cheese, beans</div><span class="price" style="left:270px">00</span></li>
    <li class="item"><div class="name">Chicken Quesadilla</div><div class="desc">served with guacamole, salsa, and sour cream</div><span class="price" style="left:270px">00</span></li>
  </ul>

  <!-- Asian mains -->
  <section class="panel" style="left:12px;top:435px;width:340px;height:346px">
    <div class="panel-dash"></div>
    <h3 style="top:28px;left:-90px">main courses</h3>
    <div class="rule" style="left:28px;top:62px;width:300px"></div>
    <div class="sprig" style="left:165px;top:57px"></div>
    <ul class="list" style="left:29px;top:74px;width:290px">
      <li class="item" style="height:77px"><div class="name">Murgh Chicken Makhni</div><div class="desc">Chicken cubes in a rich creamy tomato sauce<br>seasoned with garam masala served with<br>vegetables korma and curd rice</div><span class="price" style="left:266px">00</span></li>
      <li class="item" style="height:61px"><div class="name">Chicken Tandoori</div><div class="desc">Grilled chicken cubes with tandoori spices<br>served with basmati rice</div><span class="price" style="left:266px">00</span></li>
      <li class="item" style="height:65px"><div class="name">Thai Coconut Curry Shrimp</div><div class="desc">Sautéed shrimp tossed with curry<br>and coconut milk served with jasmine rice</div><span class="price" style="left:266px">00</span></li>
      <li class="item"><div class="name">Mongolian Beef</div><div class="desc">Soy marinated beef with oyster sauce<br>and vegetables served with egg noodles</div><span class="price" style="left:266px">00</span></li>
    </ul>
  </section>
  <div class="art" role="img" aria-label="Drawing of a wok with noodles and chopsticks" style="left:275px;top:405px;width:148px;height:95px;background:radial-gradient(ellipse,#d9cfb6 0%,#9d9483 60%,rgba(157,148,131,0) 100%)"></div>

  <!-- Tex Mex mains -->
  <section class="panel" style="left:493px;top:408px;width:339px;height:373px">
    <div class="panel-dash"></div>
    <h3 style="top:30px">main courses<br>&amp; sandwiches</h3>
    <div class="rule" style="left:27px;top:90px;width:285px"></div>
    <div class="sprig" style="left:165px;top:85px"></div>
    <ul class="list" style="left:27px;top:102px;width:285px">
      <li class="item" style="height:61px"><div class="name">Cheeseburger</div><div class="desc">House made lean beef burger<br>topped with cheddar cheese</div><span class="price" style="left:266px">00</span></li>
      <li class="item" style="height:61px"><div class="name">Mushroom Burger</div><div class="desc">Beef burger with sautéed mushroom,<br>caramelized onion, and provolone cheese</div><span class="price" style="left:266px">00</span></li>
      <li class="item" style="height:65px"><div class="name">Crispy Chicken Wrap</div><div class="desc">Crisp fried chicken wrap with<br>a ranch dressing</div><span class="price" style="left:266px">00</span></li>
      <li class="item"><div class="name">Fajita (Chicken, Beef, Combo)</div><div class="desc">Pan seared meat or chicken with onion and<br>bell pepper served with sour cream,<br>guacamole, salsa</div><span class="price" style="left:266px">00</span></li>
    </ul>
  </section>

  <!-- Desserts -->
  <div class="ribbon" style="left:235px;top:815px;width:376px"></div>
  <div class="tag" style="left:342px;top:804px;width:158px;height:43px">DESSERTS</div>
  <div class="fold" style="left:342px;top:847px;border-top:11px solid var(--fold);border-left:20px solid transparent"></div>
  <div class="fold" style="left:480px;top:847px;border-top:11px solid var(--fold);border-right:20px solid transparent"></div>

  <ul class="list" style="left:100px;top:872px;width:285px">
    <li class="item" style="height:29px"><div class="name">Mix Berries Cheesecake</div><span class="price" style="left:252px">00.00</span></li>
    <li class="item" style="height:29px"><div class="name">Crème Brulee</div><span class="price" style="left:252px">00.00</span></li>
    <li class="item" style="height:29px"><div class="name">Chocolate Caramel Cake</div><span class="price" style="left:252px">00.00</span></li>
    <li class="item" style="height:29px"><div class="name">Warm Chocolate Fondant</div><span class="price" style="left:252px">00.00</span></li>
    <li class="item" style="height:29px"><div class="name">Baked Apple Tart Tatin</div><span class="price" style="left:252px">00.00</span></li>
    <li class="item" style="height:29px"><div class="name">Tiramisu</div><span class="price" style="left:252px">00.00</span></li>
    <li class="item" style="height:29px"><div class="name">Pumpkin Pie Flan</div><span class="price" style="left:252px">00.00</span></li>
    <li class="item"><div class="name">Mixed Berries Granola Yoghurt</div><span class="price" style="left:252px">00.00</span></li>
  </ul>
  <ul class="list" style="left:460px;top:872px;width:290px">
    <li class="item" style="height:55px"><div class="name">Profiterole</div><div class="desc">Filled with vanilla ice cream<br>with dark &amp; white chocolate sauce</div><span class="price" style="left:252px">00.00</span></li>
    <li class="item" style="height:44px"><div class="name">Caramelized Banana</div><div class="desc">With deep fried ice cream</div><span class="price" style="left:252px">00.00</span></li>
    <li class="item" style="height:40px"><div class="name">Baklava</div><div class="desc">With nuts and sugar syrup</div><span class="price" style="left:252px">00.00</span></li>
    <li class="item" style="height:41px"><div class="name">Shot Glass Sampler</div><div class="desc">Tiramisu, chocolate crisp mousse, pear with sabayon</div><span class="price" style="left:252px">00.00</span></li>
    <li class="item"><div class="name">Ice Cream by Scoop</div><span class="price" style="left:252px">00.00</span></li>
  </ul>

  <div class="badge"><p>Prices are subject to <b>12% service charge</b> &amp; <b>10% sales tax</b></p></div>
</div>
</body>
</html>
```